Redesign of business card for Cedar Ridge Mechanical

We are looking for a new design for our business cards for Cedar Ridge Mechanical. We are a plumbing & HVAC construction company, operating on the West Coast of Canada and USA. Logo attached.
Industry/Entity Type
Construction - Plumbing & HVAC
Contact Information for Business Card
Name, address, phone numbers, email, website address
Look and feel
Each slider illustrates characteristics of the customer's brand and the style your logo design should communicate.

```html
<!DOCTYPE html>
<html lang="en">
<head>
<meta charset="utf-8">
<title>Cedar Ridge Mechanical – Business Card</title>
<link rel="stylesheet" href="https://fonts.googleapis.com/css2?family=Montserrat:wght@400;600;700&display=swap">
<style>
  :root {
    --page-bg: #e9e7e3;
    --card-white: #ffffff;
    --card-black: #1d1d1d;
    --ink: #1f1f1f;
    --ink-soft: #2b2b2b;
    --band-dark: #2a2a2a;
    --band-grey: #646464;
    --band-text: #f2f2f2;
    --emboss: #2e2e2e;
  }
  * { margin: 0; padding: 0; box-sizing: border-box; }
  html, body { width: 900px; height: 1200px; overflow: hidden; }
  body {
    position: relative;
    background: var(--page-bg);
    font-family: "Montserrat", Arial, sans-serif;
    color: var(--ink);
  }
  .card {
    position: absolute;
    left: 80px;
    width: 742px;
    height: 440px;
    border-radius: 22px;
    overflow: hidden;
  }
  .card--front { top: 131px; background: var(--card-white); }
  .card--back { top: 638px; background: var(--card-black); }

  .brand-name {
    position: absolute;
    left: 0; right: 0;
    text-align: center;
    font-weight: 700;
    letter-spacing: 2px;
    text-transform: uppercase;
  }
  .card--front .brand-name {
    top: 95px;
    font-size: 30px;
    color: var(--ink);
    padding-right: 28px;
  }
  .card--back .brand-name {
    top: 205px;
    font-size: 36px;
    color: var(--emboss);
    padding-right: 28px;
  }

  .person {
    position: absolute;
    right: 410px;
    top: 272px;
    text-align: right;
  }
  .person__name { font-size: 24px; font-weight: 700; line-height: 1.1; color: var(--ink-soft); }
  .person__title { font-size: 15.5px; font-weight: 400; margin-top: 6px; color: var(--ink-soft); }

  .divider {
    position: absolute;
    left: 356px;
    top: 267px;
    width: 2px;
    height: 82px;
    background: var(--ink-soft);
  }

  .contacts {
    position: absolute;
    left: 374px;
    top: 263px;
    list-style: none;
  }
  .contacts li {
    display: flex;
    align-items: center;
    height: 30.5px;
    font-size: 15.5px;
    color: var(--ink-soft);
  }
  .contacts svg { width: 16px; height: 16px; margin-right: 10px; flex: none; }

  .address-band {
    position: absolute;
    left: 0;
    top: 371px;
    width: 742px;
    height: 35px;
  }
  .address-band__text {
    position: absolute;
    left: 0;
    width: 690px;
    top: 371px;
    height: 35px;
    line-height: 35px;
    text-align: center;
    font-size: 16px;
    color: var(--band-text);
    padding-right: 190px;
  }
</style>
</head>
<body>

  <section class="card card--front" aria-label="Business card front">
    <div class="brand-name">Cedar Ridge Mechanical</div>

    <div class="person">
      <div class="person__name">Daniel Hayes</div>
      <div class="person__title">Managing Director</div>
    </div>

    <div class="divider"></div>

    <ul class="contacts">
      <li>
        <svg viewBox="0 0 24 24" aria-hidden="true"><path fill="#2b2b2b" d="M6.6 10.8a15.1 15.1 0 0 0 6.6 6.6l2.2-2.2c.3-.3.7-.4 1-.2 1.1.4 2.3.6 3.6.6.6 0 1 .4 1 1V20c0 .6-.4 1-1 1A17 17 0 0 1 3 4c0-.6.4-1 1-1h3.5c.6 0 1 .4 1 1 0 1.3.2 2.5.6 3.6.1.3 0 .7-.2 1z"/><path fill="none" stroke="#2b2b2b" stroke-width="1.8" d="M14 3.5a7 7 0 0 1 6.5 6.5M14 7a3.5 3.5 0 0 1 3 3"/></svg>
        555.214.7730
      </li>
      <li>
        <svg viewBox="0 0 24 24" aria-hidden="true"><path fill="#2b2b2b" d="M3 5h18v14H3z"/><path fill="none" stroke="#fff" stroke-width="1.6" d="M3.5 6l8.5 7 8.5-7"/></svg>
        info@cedarridgemechanical.com
      </li>
      <li>
        <svg viewBox="0 0 24 24" aria-hidden="true"><circle cx="12" cy="12" r="10" fill="#2b2b2b"/><path fill="#fff" d="M8 6.5c1.5.5 2 1.8 1.5 3-.6 1.2-2 1-2.5 2.5-.4 1.2.8 2.5.3 4C6 15 5 13 5 12c0-2.3 1.2-4.3 3-5.5zm7 3c1.5-.2 2.8.8 2.5 2.5-.2 1.3-1.6 1.6-1.5 3 .1 1.2-.5 2.3-1.6 3-.6-1.5-.2-2.7-1-3.6-.8-.9-.6-2.1.2-2.8.5-.5.7-1.3 1.4-2.1z"/></svg>
        www.cedarridgemechanical.com
      </li>
    </ul>

    <svg class="address-band" viewBox="0 0 742 35" aria-hidden="true">
      <polygon points="0,0 545,0 527,35 0,35" fill="var(--band-dark)"/>
      <polygon points="555,0 742,0 742,35 537,35" fill="var(--band-grey)"/>
    </svg>
    <div class="address-band__text">48 Harbor View Road Bellingham, WA 98225</div>
  </section>

  <section class="card card--back" aria-label="Business card back">
    <div class="brand-name">Cedar Ridge Mechanical</div>
  </section>

</body>
</html>
```